Support People to improve their image and well-being by provided personalised advise

We need a design for business cards that could be used for production on plano press. We build a new business in our region for advising mostly women (also men though) on style embracing several aspects including fashion, style, self-confidence and ultimately your internal and external image. The business card should be "classy", "french-style". The business is located in the french -speaking part of Switzerland, close to France. The name of the company is Lomu Grace

Target Market(s)

Service fees won't be cheap (medium to premium) thus we target mid-class to upper-class women (1st target) and men (2nd target)

Industry/Entity Type

Life Coaching

Contact Information for Business Card

Conseil en Image

+41 76 418 63 07
tovasel@lomu-grace.example
linkedin.example/in/sel-moran-tova

Logo Text

Lomu Grace

Colors

Designer to choose colors to be used in the design.

```html
<!DOCTYPE html>
<html lang="fr">
<head>
<meta charset="utf-8">
<title>Lomu Grace – Cartes de visite</title>
<link rel="stylesheet" href="https://fonts.googleapis.com/css2?family=Jost:wght@400;500&family=Kaushan+Script&display=swap">
<style>
  :root {
    --backdrop: #c4c4c4;
    --card: #363a3e;
    --card-edge: #2e3135;
    --gold-light: #e6c898;
    --gold: #cfaa78;
    --gold-deep: #b48d5f;
    --text-light: #e4e4e4;
    --text-muted: #c9c9c9;
  }
  * { margin: 0; padding: 0; box-sizing: border-box; }
  html, body {
    width: 1200px; height: 576px; overflow: hidden;
    background: var(--backdrop);
  }
  .sheet { position: relative; width: 1200px; height: 576px; }
  .card {
    position: absolute; top: 138px;
    width: 482px; height: 294px;
    border-radius: 13px;
    background: var(--card);
    overflow: hidden;
  }
  .card--front { left: 82px; }
  .card--back { left: 602px; }

  .wordmark {
    font-family: "Jost", sans-serif;
    font-weight: 500;
    color: var(--text-light);
    letter-spacing: 0.2em;
    text-transform: uppercase;
    white-space: nowrap;
  }

  /* front */
  .front-dot {
    position: absolute; left: 50%; top: 112px;
    width: 44px; height: 44px; margin-left: -22px;
    border-radius: 50%;
    background: linear-gradient(160deg, var(--gold-light), var(--gold-deep));
  }
  .card--front .wordmark {
    position: absolute; left: 0; right: 0; top: 182px;
    text-align: center; font-size: 27px;
    padding-left: 0.2em;
  }

  /* back */
  .gold-band {
    position: absolute; left: 42px; top: 26px; bottom: 0;
    width: 58px;
    border-radius: 6px 6px 0 0;
    background: linear-gradient(180deg, var(--gold-light), var(--gold-deep));
  }
  .card--back .wordmark {
    position: absolute; left: 260px; top: 46px;
    font-size: 25px;
  }
  .person { position: absolute; left: 260px; top: 128px; }
  .person__name {
    font-family: "Kaushan Script", cursive;
    font-size: 23px; color: var(--gold);
    line-height: 1.2;
  }
  .person__role {
    font-family: "Jost", sans-serif;
    font-size: 13px; color: var(--text-muted);
    margin-top: 2px;
  }
  .contact {
    position: absolute; left: 264px; top: 196px;
    list-style: none;
    font-family: "Jost", sans-serif;
    font-size: 13.5px; color: var(--text-muted);
  }
  .contact__item {
    display: flex; align-items: center;
    height: 18px;
  }
  .contact__icon {
    width: 11px; height: 11px; margin-right: 9px;
    fill: var(--text-muted);
    flex: none;
  }
</style>
</head>
<body>
<main class="sheet">
  <section class="card card--front" aria-label="Recto">
    <div class="front-dot"></div>
    <p class="wordmark">Lomu Grace</p>
  </section>

  <section class="card card--back" aria-label="Verso">
    <div class="gold-band"></div>
    <p class="wordmark">Lomu Grace</p>
    <div class="person">
      <p class="person__name">Tova Sel Moran</p>
      <p class="person__role">Managing Director</p>
    </div>
    <ul class="contact">
      <li class="contact__item">
        <svg class="contact__icon" viewBox="0 0 12 12" aria-hidden="true">
          <path d="M1 4c0-2 2-3 5-3s5 1 5 3v1H8V4H4v1H1z"/>
          <rect x="2" y="6" width="8" height="5" rx="1"/>
        </svg>
        +41 76 418 63 07
      </li>
      <li class="contact__item">
        <svg class="contact__icon" viewBox="0 0 12 12" aria-hidden="true">
          <path d="M0 2h12v1L6 7 0 3z"/>
          <path d="M0 4.5l6 4 6-4V10H0z"/>
        </svg>
        tovasel@lomu-grace.example
      </li>
      <li class="contact__item">
        <svg class="contact__icon" viewBox="0 0 12 12" aria-hidden="true">
          <circle cx="6" cy="6" r="5.5"/>
          <path d="M6 0.5v11M0.5 6h11M6 0.5c-3 3-3 8 0 11M6 0.5c3 3 3 8 0 11" stroke="#363a3e" stroke-width="0.8" fill="none"/>
        </svg>
        www.lomu-grace.example
      </li>
    </ul>
  </section>
</main>
</body>
</html>
```